Maple Beacon Website

We are starting a marketing company and to do that we need a website! We want a website that will inspire and persuade to bring out the awesomeness in our clients.
What we want to see:
- Inspirational and persuasive imagery that relate to Branding.
- No cliche images eg. business man, suits and hand shakes
- We want to transform and educate our clients.
- We want to show them the path and would like our website to really act as a guide that guides them step by step through our process.
- We want the portray that we are an investment but not have a pretentious way to it. We put our heart into every project and that is how we treat our clients.
-When you submit your design please include what platform you have created for. Preference would be Wordpress or Joobla.

We have included the psd file for the wire frame, logo files, font files, site map and a link to a video we create to give you more information on what we would like to see. http://clipvault.example/t/qk82LmZpr

Feel free to make small modification to the logos if you think it will improve it. Your creativity and advice is most welcome.
Updates

One thing we forgot. We would like to have our contact information near the top of the website as well as at the bottom.  Here is out contact info:

Email: info@maplebeacon.example
Phone: 587-555-0142

Project Deadline Extended
Reason: As we are new with the platform and that we want to optimize our results, we decided to extend the deadline by 15 days. Thanks!

Target Market(s)

28-60, Male and Female, Oil field, Local Businesses, Dentists, Chiropractors, Hair salon, Construction/Renovation, Events etc

Industry/Entity Type

Investment

Requirements
Must have
• - 4 Inspirational and persuasive Imagery for the top portion of the website
- Must have a feel as if your not on a website an example of this is linked below.
http://www.artbidhub.example/design/402957/web-design-by-lena-torvik
Nice to have
• - Creative advice from you.
- Creative buttons for Get Free Quote and Subscribe buttons. Something out of the box that draws peoples attention. eg. a 'B' button. Just and example but still something related to branding.
Should not have
• No Cliches

```html
<!DOCTYPE html>
<html lang="en">
<head>
<meta charset="utf-8">
<title>Maple Beacon — Strategy</title>
<link rel="stylesheet" href="https://fonts.googleapis.com/css2?family=Arimo:wght@400;700&display=swap">
<style>
  :root {
    --ink-dark: #2f3140;
    --top-active: #4a4e63;
    --nav-muted: #8d909e;
    --tab-dark: rgba(40, 42, 56, 0.78);
    --tab-divider: rgba(160, 170, 220, 0.35);
    --green-top: #9bc45a;
    --green-bottom: #6a9a2a;
    --green-edge: #5e8a24;
    --body-grey: #8a8a8a;
    --link-blue: #2a8ad8;
    --panel-grey: #f1f1f1;
    --footer-muted: #7a7d90;
    --white: #ffffff;
  }
  * { box-sizing: border-box; margin: 0; padding: 0; }
  html, body { width: 1200px; height: 823px; overflow: hidden; }
  body {
    position: relative;
    background: var(--white);
    font-family: "Arimo", Arial, sans-serif;
    color: var(--body-grey);
  }

  /* Top bar */
  .top-bar {
    position: absolute; left: 0; top: 0; width: 1200px; height: 40px;
    background: var(--ink-dark); z-index: 2;
  }
  .top-nav { position: absolute; left: 330px; top: 0; display: flex; height: 40px; }
  .top-nav a {
    display: block; height: 40px; line-height: 42px;
    text-align: center; font-size: 17px; font-weight: 700;
    color: var(--nav-muted); text-decoration: none; position: relative;
  }
  .top-nav a:nth-child(1) { width: 162px; }
  .top-nav a:nth-child(2) { width: 140px; }
  .top-nav a:nth-child(3) { width: 142px; }
  .top-nav a:nth-child(4) { width: 150px; }
  .top-nav a.is-active { background: var(--top-active); color: var(--white); }
  .top-nav a.is-active::after {
    content: ""; position: absolute; left: 64px; bottom: -7px;
    border-left: 7px solid transparent; border-right: 7px solid transparent;
    border-top: 7px solid var(--top-active);
  }
  .social-links { position: absolute; left: 955px; top: 10px; display: flex; gap: 6px; }
  .social-links span {
    width: 24px; height: 24px; border-radius: 4px; background: var(--nav-muted);
  }

  /* Brand tile */
  .brand-tile {
    position: absolute; left: 118px; top: 0; width: 189px; height: 76px;
    background: var(--white); z-index: 3;
    box-shadow: 0 2px 6px rgba(0, 0, 0, 0.35);
    display: flex; align-items: center; justify-content: center;
  }
  .brand-name {
    font-size: 20px; font-weight: 700; color: var(--ink-dark); white-space: nowrap;
  }

  /* Hero */
  .hero-image {
    position: absolute; left: 0; top: 40px; width: 1200px; height: 295px;
    background:
      linear-gradient(160deg, rgba(150, 160, 230, 0.85) 0%, rgba(110, 115, 200, 0.6) 35%, rgba(40, 48, 60, 0.7) 60%, rgba(120, 125, 210, 0.8) 100%),
      linear-gradient(90deg, #7d82cf, #3b4350 50%, #8a8fd8);
  }

  /* Main tabs */
  .main-nav { position: absolute; left: 117px; top: 274px; display: flex; height: 61px; }
  .main-nav a {
    display: flex; align-items: center; justify-content: center;
    width: 160px; height: 61px; background: var(--tab-dark);
    box-shadow: inset -1px 0 0 var(--tab-divider);
    color: var(--white); font-size: 21px; font-weight: 700; text-decoration: none;
  }
  .main-nav a.is-active { background: var(--white); color: var(--ink-dark); box-shadow: none; }
  .main-nav a.quote-button {
    margin-left: 2px; width: 159px;
    background: linear-gradient(var(--green-top), var(--green-bottom));
    box-shadow: inset 0 0 0 1px var(--green-edge);
    font-size: 18px; line-height: 18px; text-align: center;
  }

  /* Content */
  .page-content { position: absolute; left: 158px; top: 367px; width: 560px; }
  .page-content h1 { font-size: 23px; font-weight: 700; color: var(--ink-dark); margin-bottom: 13px; }
  .page-content p { font-size: 15.5px; line-height: 22px; margin-bottom: 22px; }
  .page-content a { color: var(--link-blue); text-decoration: underline; }

  .newsletter-panel {
    position: absolute; left: 760px; top: 408px; width: 285px; height: 166px;
    background: var(--panel-grey); border-radius: 6px; padding: 27px 0 0 50px;
  }
  .newsletter-panel h2 { font-size: 21px; font-weight: 700; color: #3a3a3a; }
  .newsletter-panel p { font-size: 15px; color: #777; margin-top: 4px; }
  .subscribe-button {
    display: block; width: 191px; height: 46px; margin-top: 16px;
    background: linear-gradient(var(--green-top), var(--green-bottom));
    border: 1px solid var(--green-edge); color: var(--white);
    font-size: 21px; font-weight: 700; text-align: center; line-height: 44px; text-decoration: none;
  }

  /* Footer */
  .site-footer {
    position: absolute; left: 0; top: 727px; width: 1200px; height: 96px;
    background: var(--ink-dark);
  }
  .footer-nav { position: absolute; left: 117px; top: 15px; display: flex; gap: 14px; }
  .footer-nav a { color: var(--white); font-size: 15.5px; text-decoration: none; }
  .copyright { position: absolute; right: 139px; top: 17px; font-size: 13px; color: var(--footer-muted); }
</style>
</head>
<body>
  <header class="top-bar">
    <nav class="top-nav">
      <a href="#">Maple Beacon</a>
      <a href="#">Be Found</a>
      <a href="#" class="is-active">Connect</a>
      <a href="#">Get Growing</a>
    </nav>
    <div class="social-links" aria-label="Social links">
      <span></span><span></span><span></span><span></span>
    </div>
  </header>

  <div class="brand-tile">
    <span class="brand-name">Maple Beacon</span>
  </div>

  <div class="hero-image" role="img" aria-label="Close view of woven white rope netting in cool blue light"></div>

  <nav class="main-nav">
    <a href="#" class="is-active">Strategy</a>
    <a href="#">Portfolio</a>
    <a href="#">About Us</a>
    <a href="#">Contact Us</a>
    <a href="#">Blog</a>
    <a href="#" class="quote-button">Get a<br>Free Quote</a>
  </nav>

  <main class="page-content">
    <h1>Main Headline</h1>
    <p>Morbi ac commodo nulla. In condimentum orci id nisl volutpat bibendum. Quisque commodo hendrerit lorem quis egestas. Maecenas quis tortor arcu. Vivamus rutrum nunc non neque consectetur quis placerat neque lobortis.</p>
    <p>Nam vestibulum, arcu sodales feugiat consectetur, nisl orci bibendum elit, eu euismod magna sapien ut nibh. Donec <a href="#">sample link</a> tortor dictum gravida. In hac habitasse platea dictumst. Nam pulvinar, odio sed rhoncus suscipit, sem diam ultrices mauris, eu consequat purus metus eu velit. Proin metus odio, aliquam eget molestie nec, gravida ut sapien.</p>
    <p>Phasellus quis est sed turpis sollicitudin venenatis sed eu odio. Praesent eget neque.</p>
  </main>

  <aside class="newsletter-panel">
    <h2>Get Tips and Tricks!</h2>
    <p>Subscribe to our Newsletter.</p>
    <a href="#" class="subscribe-button">Subscribe</a>
  </aside>

  <footer class="site-footer">
    <nav class="footer-nav">
      <a href="#">Site Map</a>
      <a href="#">Strategy</a>
      <a href="#">Portfolio</a>
      <a href="#">About Us</a>
      <a href="#">Contact Us</a>
      <a href="#">Blog</a>
    </nav>
    <p class="copyright">©MAPLE BEACON INC. 2013</p>
  </footer>
</body>
</html>
```